Velvet Lantern rebranding my business with a new business card

I have my new logo and now I need a refresher on my business cards. I really want something fun and fresh. I like black background or anything to make the color pop.
Logo
Name: Velvet Lantern
Contact Info as stated below:
Mira Pellow
555-013-4762
Logo
Name: Velvet Lantern
Mira Pellow
555-013-4762
page.vl/VelvetLanternbyMira
Instagram: @VelvetLanternbyMira

Industry/Entity Type

Business

Contact Information for Business Card

double-sided. Logo on one side. Contact info on the other.

Requirements
Must have
• Logo
• Name: Velvet Lantern
• Contact Info as stated below:
• Mira Pellow
• 555-013-4762
• page.vl/VelvetLanternbyMira
• page.vl/VelvetLanternbyMira

```html
<!DOCTYPE html>
<html lang="en">
<head>
<meta charset="utf-8">
<title>Velvet Lantern – Business Card</title>
<link rel="stylesheet" href="https://fonts.googleapis.com/css2?family=Roboto:wght@400;500&family=Roboto+Condensed:wght@700&display=swap">
<style>
  :root {
    --backdrop: #e8e5e1;
    --card-pink: #f0a6b5;
    --card-white: #f3f3f3;
    --band-black: #050505;
    --ink: #111111;
    --text-grey: #5a5a5a;
    --url-grey: #7b6a6f;
    --ring-pink: #f2b4c2;
    --brand-rose: #9c3b55;
    --icon-white: #ffffff;
  }
  * { margin: 0; padding: 0; box-sizing: border-box; }
  html, body {
    width: 1200px; height: 960px; overflow: hidden;
    background: var(--backdrop);
  }
  .canvas { position: relative; width: 1200px; height: 960px; }

  .card {
    position: absolute; left: 320px; width: 600px;
    border-radius: 18px; overflow: hidden;
    box-shadow: 0 4px 10px rgba(0,0,0,0.18);
  }

  /* Front: logo side */
  .card-front { top: 100px; height: 350px; background: var(--card-pink); }
  .front-brand {
    position: absolute; left: 0; right: 0; top: 150px;
    display: flex; align-items: center; justify-content: center; gap: 12px;
  }
  .brand-dot {
    width: 26px; height: 26px; border-radius: 50%;
    background: var(--brand-rose);
  }
  .brand-name {
    font-family: "Roboto", sans-serif; font-weight: 500;
    font-size: 34px; color: var(--brand-rose); letter-spacing: 1px;
  }
  .front-url {
    position: absolute; left: 0; right: 0; top: 298px; text-align: center;
    font-family: "Roboto", sans-serif; font-size: 14px;
    letter-spacing: 7px; color: var(--url-grey);
  }

  /* Back: contact side */
  .card-back { top: 493px; height: 342px; background: var(--card-white); }
  .side-band {
    position: absolute; left: 0; top: 0; bottom: 0; width: 135px;
    background: var(--band-black);
  }
  .logo-badge {
    position: absolute; left: 1px; top: 7px; width: 134px; height: 134px;
    border-radius: 50%; background: #ffffff;
    border: 3px solid var(--ring-pink);
    box-shadow: 0 0 0 2px var(--band-black);
    display: flex; align-items: center; justify-content: center; text-align: center;
  }
  .badge-name {
    font-family: "Roboto", sans-serif; font-weight: 500;
    font-size: 15px; line-height: 1.2; color: var(--brand-rose);
  }
  .contact-icons {
    position: absolute; left: 55px; top: 208px;
    display: flex; flex-direction: column; gap: 13px;
  }
  .contact-icons svg { display: block; width: 25px; height: 25px; }

  .holder-name {
    position: absolute; left: 169px; top: 66px;
    font-family: "Roboto Condensed", sans-serif; font-weight: 700;
    font-size: 22px; color: var(--ink); letter-spacing: 0.2px;
  }
  .contact-list {
    position: absolute; left: 169px; top: 211px; list-style: none;
    font-family: "Roboto", sans-serif; font-size: 14.5px; color: var(--text-grey);
  }
  .contact-list li { height: 38px; line-height: 20px; }
</style>
</head>
<body>
<main class="canvas">

  <section class="card card-front" aria-label="Card front">
    <div class="front-brand">
      <span class="brand-dot"></span>
      <span class="brand-name">Velvet Lantern</span>
    </div>
    <p class="front-url">www.velvetlantern.com</p>
  </section>

  <section class="card card-back" aria-label="Card back">
    <div class="side-band">
      <div class="contact-icons">
        <svg viewBox="0 0 24 24" aria-label="Phone">
          <circle cx="12" cy="12" r="12" fill="var(--icon-white)"/>
          <path d="M8.3 6.2c.4-.3 1-.3 1.3.1l1.4 1.9c.3.4.2.9-.1 1.2l-.9.8c.6 1.4 1.6 2.5 3 3.2l.8-.9c.3-.3.8-.4 1.2-.1l1.9 1.3c.4.3.5.9.1 1.3l-.8.9c-.6.6-1.5.8-2.3.5-3-1.2-5.3-3.5-6.4-6.5-.3-.8-.1-1.7.5-2.3z" fill="var(--band-black)"/>
        </svg>
        <svg viewBox="0 0 24 24" aria-label="Website">
          <circle cx="12" cy="12" r="12" fill="var(--icon-white)"/>
          <circle cx="12" cy="12" r="5.8" fill="none" stroke="var(--band-black)" stroke-width="1.6"/>
          <path d="M6.2 12h11.6M12 6.2c-2 2-2 9.6 0 11.6M12 6.2c2 2 2 9.6 0 11.6" fill="none" stroke="var(--band-black)" stroke-width="1.2"/>
        </svg>
        <svg viewBox="0 0 24 24" aria-label="Social page">
          <circle cx="12" cy="12" r="12" fill="var(--icon-white)"/>
          <rect x="7" y="7" width="10" height="10" rx="1.5" fill="var(--band-black)"/>
        </svg>
      </div>
    </div>
    <div class="logo-badge">
      <span class="badge-name">Velvet<br>Lantern</span>
    </div>

    <h1 class="holder-name">MIRA PELLOW</h1>
    <ul class="contact-list">
      <li>555-013-4762</li>
      <li>www.velvetlantern.com</li>
      <li>page.vl/VelvetLanternbyMira</li>
    </ul>
  </section>

</main>
</body>
</html>
```